Cannabis Media Network Advertising Kit

Polar Orbit Media is a digital media news network focused on the startups, entrepreneurs and innovative companies in the cannabis industry. We are ready to release our new services for 2017.

We are looking for a modern looking advertising kit created that we would send to our potential clients.

We want it to look similar to our branding. Our website is www.polarorbitmedia.example.

Target Market(s)

Page 3: Audience:
Entrepreneurs, professionals, execs, VC’s, and Investors
Include stats: 34% Female/ 66% Male, 34% 25-34 Years Old $24% 35-44 Years Old

Industry/Entity Type

Media

Font styles to use
Sans Serif

Colors
0555a3
0492cd
ffffff
edf1f7

Requirements
Must have
• Outline Idea is below. Images can be provided.
• Page 1: Header Page (POM logo)
• Leading digital media news network covering the latest tech, startups, and innovative companies in the cannabis industry.
• Page 2: About Us - Mission and Brand
• Polar Orbit Media is the leading digital media platform that is dedicated to profiling the startups, entrepreneurs and innovative companies in the cannabis industry.
• Over the past few years we have been highlighting the upcoming and established businesses in the industry, developed a platform for leaders to share their knowledge and insight, and created
• a spotlight for the innovative technology.
• But most importantly, we have created a community of entrepreneurs, investors and professionals who have the same mission of growing the b2b industry together.
• POM is more than just a network and brand, we are highlighting history in the making of high quality original content.
• Page 3: Audience:
• Entrepreneurs, professionals, execs, VC’s, and Investors
• Include stats: 34% Female/ 66% Male, 34% 25-34 Years Old $24% 35-44 Years Old
• Page 4: POM Original Web Series
• Pre/Post Commercial Opportunities $5,000
• Tinbell Reviews and POM Talks
• Tinbell Reviews is a un-biased product review segment for the wholesalers, online stores, dispensaries and more.
• POM Talks: One on one interview with the upcoming and leading founders offering advice and insight for fellow entrepreneurs.
• Page 5: POM Original Web Series
• Kettles and Kites is a female founder focused web series, where we highlight the leaders, discuss informative topics and latest products.
• Product placement $2,500
• Page 6: POM Original Web Series
• Upside Ledge gives you a peek into the entrepreneur 2.0 and what it is like running a cannabis business.
• See leadership package
• Page 7: Package 1: Foundation $1,000
• 1. Four full platform ads (via QT, ZR, Plonkit, Fernwork, Braxtile)
• 2. POM Article/Company Spotlight (One Newsletter feature and full POM promotion)
• 3. Newsletter Ad (One run, assets provided by client
• Page 8: Package 2: Traction $5,000
• 1. Six full platform ads (via QT, ZR, Plonkit, Fernwork, Braxtile)
• 4. Business of the Month Badge (POM Homepage)
• 5. Three Verbal Video Advertisements ( Three segments, up to 10 seconds each)
• Page 9: Package 3: Leadership $15,000
• 5. Three Video Advertisements (Three segments, 30 second commercial)
• 7. Upside Ledge Full Segment
• Includes promo and full segment promoted and released via POM.
• Page 10: Events Promotion
• Event Package $1,000
• 1. Four full platform ads (via QT include QT Event on POM Page, ZR, Plonkit, Fernwork, Braxtile)
• A la Carte:
• Add event to POM calendar, basic promotion via social media $250
• POMTV Media Sponsor
• Includes co-branded video production of event, exclusive interview with sponsors, and more
• *Cost: To Be Determined
• Page 11: A La Carte
• 1. Event Addition to Calendar (Basic promotion via social media)
• 2. Six full platform ads (via QT, ZR, Plonkit, Fernwork, Braxtile)
• 3. POM Article/Company Spotlight (One Newsletter feature and full POM promotion)
• 4. Newsletter Ad (One run, assets provided by client
• 5. Business of the Month Badge (POM Homepage)
• 6. Three Verbal Video Advertisements ( Three segments, up to 10 seconds each)
• Page 12: Traction
• Profiled on fernwork, orbel daily, spindara, quillstoa, plonkit, zephrame
• 10k+ organic email list of professionals
• 16k+ page views increasing 25% each month
• 18k+ social media followers
• Viewed in all 50 states and 98 countries
• Page 13: Message from the CEO
• “We at POM understand that our industry is different than any other industry out there, we even look at the entrepreneurs and don’t see them just as an entrepreneur but as an entrepreneur 2.0. Why? Because this is the first time in a long time where we have the opportunity to change how an industry is built from the foundation up and each of these individuals are faced with hurdles and challenges we wouldn’t face in any other industry and yet they are doing what it takes to continue to move forward.”
• Page 14: Contact Us
• POM logo:
• We look forward to growing your brand with the Polar Orbit Media! Contact us today at contact@polarorbitmedia.example
Nice to have
• High Res Images from our content. Which we can provide those images, or you can pull from our site and we can send high res after.
Should not have
• Dark Designed.

```html
<!DOCTYPE html>
<html lang="en">
<head>
<meta charset="utf-8">
<title>Polar Orbit Media — A La Carte</title>
<link rel="stylesheet" href="https://fonts.googleapis.com/css2?family=Open+Sans:wght@300;400;700&display=swap">
<style>
  :root {
    --brand-navy: #0555a3;
    --brand-sky: #0492cd;
    --brand-white: #ffffff;
    --page-bg: #edf1f7;
    --ink: #3a3d44;
  }
  html, body {
    margin: 0;
    padding: 0;
    overflow: hidden;
    background: var(--page-bg);
  }
  .page {
    position: relative;
    width: 1200px;
    height: 900px;
    overflow: hidden;
    background: var(--page-bg);
    font-family: "Open Sans", Arial, sans-serif;
    color: var(--ink);
  }
  .page-art {
    position: absolute;
    inset: 0;
    width: 1200px;
    height: 900px;
  }
  .section-title {
    position: absolute;
    left: 52px;
    top: 180px;
    width: 200px;
    margin: 0;
    text-align: center;
    font-size: 24px;
    line-height: 26px;
    font-weight: 700;
    color: var(--brand-navy);
    letter-spacing: -0.3px;
  }
  .service-list {
    position: absolute;
    left: 448px;
    top: 214px;
    margin: 0;
    padding: 0;
    list-style: none;
    counter-reset: service;
  }
  .service-item {
    counter-increment: service;
    position: relative;
    padding-left: 22px;
    margin-bottom: 13px;
    font-size: 20px;
    line-height: 34px;
    font-weight: 300;
  }
  .service-item::before {
    content: counter(service) ".";
    position: absolute;
    left: 0;
    top: 0;
    font-weight: 700;
    color: var(--brand-sky);
  }
  .service-name, .service-detail {
    display: block;
  }
  .brand-mark {
    position: absolute;
    left: 1100px;
    top: 805px;
    font-size: 20px;
    font-weight: 700;
    color: var(--brand-navy);
  }
  .page-number {
    position: absolute;
    left: 1146px;
    top: 848px;
    font-size: 19px;
    font-weight: 300;
    color: var(--ink);
  }
</style>
</head>
<body>
<main class="page">
  <svg class="page-art" viewBox="0 0 1024 768" aria-hidden="false">
    <defs>
      <linearGradient id="corner-blue" x1="0" y1="0" x2="1" y2="1">
        <stop offset="0" stop-color="#2f7fcf"/>
        <stop offset="0.55" stop-color="#3a95dc"/>
        <stop offset="1" stop-color="#1f6dbd"/>
      </linearGradient>
    </defs>
    <path class="corner-panel" role="img" aria-label="Faceted blue geometric backdrop"
          d="M0 0 H235 L182 58 A128 128 0 1 1 50 268 L0 318 Z" fill="url(#corner-blue)"/>
    <circle class="corner-ring" cx="130" cy="178" r="124" fill="none" stroke="#ffffff" stroke-width="5"/>
    <circle class="title-badge" cx="130" cy="178" r="88" fill="#ffffff"/>
    <line class="accent-stripe" x1="250" y1="0" x2="190" y2="64" stroke="#0555a3" stroke-width="4"/>
    <line class="accent-stripe" x1="44" y1="282" x2="0" y2="332" stroke="#0492cd" stroke-width="4"/>
    <line class="accent-stripe" x1="1024" y1="588" x2="918" y2="768" stroke="#0492cd" stroke-width="4"/>
    <line class="accent-stripe" x1="1024" y1="655" x2="958" y2="768" stroke="#0555a3" stroke-width="3"/>
  </svg>

  <h1 class="section-title">A LA<br>CARTE</h1>

  <ol class="service-list">
    <li class="service-item">
      <span class="service-name">Event Addition to Calendar</span>
      <span class="service-detail">(Basic promotion via social media)</span>
    </li>
    <li class="service-item">
      <span class="service-name">Six full platform ads</span>
      <span class="service-detail">(via QT, ZR, Plonkit, Fernwork, Braxtile)</span>
    </li>
    <li class="service-item">
      <span class="service-name">POM Article/Company Spotlight</span>
      <span class="service-detail">(One Newsletter feature and full POM promotion)</span>
    </li>
    <li class="service-item">
      <span class="service-name">Newsletter Ad</span>
      <span class="service-detail">(One run, assets provided by client</span>
    </li>
    <li class="service-item">
      <span class="service-name">Business of the Month Badge</span>
      <span class="service-detail">(POM Homepage)</span>
    </li>
    <li class="service-item">
      <span class="service-name">Three Verbal Video Advertisements</span>
      <span class="service-detail">(Three segments, up to 10 seconds each)</span>
    </li>
  </ol>

  <div class="brand-mark">POM</div>
  <div class="page-number">11</div>
</main>
</body>
</html>
```